Stationery Design Project for Nimbora, Chicago

Nimbora, a street parking application which helps car drivers find a street parking spot by offering an ideal path along which to look for parking. This path is calculated by our algorithm based on data (e.g. historical data, baseball games schedule, etc.). Along this path the driver will find a spot and will also save 70% of the search time. Customer we target is reg. between 21 and 45 yo.

We envision something young, fresh, bright and original. Slightly abstract maybe. It should represent the idea and elements of finding street parking in the city, e.g. car(s), parking spot, people, city, etc. (just ideas!).

Logo is attached.

Requirement:
- Business Cards (2 Sided Full Color CMYK)
- Letterhead (1 Sided Full Color CMYK)
- Envelope (1 Sided Full Color CMYK)
- Sticker (1 Sided Full Color CMYK), round with a 2inch diameter.

Reason: We're starting to get more and more designs and need more time to look into all of them. Very exciting!! Thanks to everybody!

Hi all, we're in the process of selecting our favs. Though choices!!! Really good submissions. Will keep you posted and sorry for the delay.

Target Market(s)

Car drivers and owners between 21 and 45

Industry/Entity Type

Parking

Requirements
Must have
• Sticker should be round and include company URL nimbora.com and the new logo which we will attach soon.
Should not have
• Should not be too serious or boring.

```html
<!DOCTYPE html>
<html lang="en">
<head>
<meta charset="utf-8">
<title>Nimbora Business Card</title>
<link rel="stylesheet" href="https://fonts.googleapis.com/css2?family=Open+Sans:wght@400;600;700&display=swap">
<style>
  :root {
    --bg: #e9e7e4;
    --white: #ffffff;
    --blue-deep: #2a4fb8;
    --blue-mid: #2f78cc;
    --blue-light: #34a6e2;
    --ink: #1c1c1c;
    --bar-dark: #0e0e0e;
    --bar-grey: #5d5d5d;
    --rule: #3a3a3a;
    --photo-grey: #9aa0a6;
    --photo-dark: #5b6068;
  }
  * { box-sizing: border-box; margin: 0; padding: 0; }
  html, body {
    width: 1200px; height: 758px; overflow: hidden;
    background: var(--bg);
    font-family: "Open Sans", Arial, sans-serif;
  }
  .canvas {
    position: relative; width: 1200px; height: 758px;
  }
  .card {
    position: absolute; top: 224px;
    width: 540px; height: 310px;
    border-radius: 22px; overflow: hidden;
    box-shadow: 0 6px 18px rgba(0,0,0,0.18);
  }
  /* Front */
  .card--front { left: 40px; background: var(--white); }
  .front__top {
    position: absolute; left: 0; top: 0; width: 100%; height: 176px;
    background: var(--white);
  }
  .front__rule {
    position: absolute; left: 0; top: 176px; width: 100%; height: 3px;
    background: var(--rule);
  }
  .front__band {
    position: absolute; left: 0; top: 182px; width: 100%; height: 128px;
    background: linear-gradient(180deg, var(--blue-mid) 0%, var(--blue-deep) 45%, var(--blue-light) 100%);
  }
  .brand {
    position: absolute; top: 50px; left: 0; width: 100%;
    display: flex; align-items: center; justify-content: center; gap: 18px;
  }
  .brand__dot {
    width: 78px; height: 78px; border-radius: 50%;
    background: var(--blue-deep);
  }
  .brand__name {
    font-size: 58px; font-weight: 600; color: var(--ink);
    letter-spacing: 0.5px; line-height: 1;
  }
  .name-bar {
    position: absolute; left: 168px; top: 158px; width: 300px; height: 38px;
    background: linear-gradient(90deg, var(--bar-dark) 0%, var(--bar-dark) 55%, var(--bar-grey) 100%);
    display: flex; align-items: center; padding-left: 42px;
    color: var(--white); font-size: 19px; letter-spacing: 1.5px;
  }
  .name-bar strong { font-weight: 700; }
  .name-bar span { font-weight: 400; margin-left: 6px; }
  .address {
    position: absolute; right: 280px; top: 236px;
    text-align: right; color: var(--white); font-size: 13.5px; line-height: 1.45;
  }
  .contact-divider {
    position: absolute; left: 272px; top: 200px; width: 1px; height: 90px;
    background: rgba(255,255,255,0.55);
  }
  .contacts {
    position: absolute; left: 282px; top: 200px;
    list-style: none; color: var(--white); font-size: 13.5px; line-height: 1.6;
  }
  .contacts li { display: flex; align-items: center; gap: 7px; }
  .contacts svg { width: 11px; height: 11px; fill: var(--white); flex: none; }
  /* Back */
  .card--back {
    left: 620px;
    background: linear-gradient(180deg, var(--blue-deep) 0%, var(--blue-mid) 50%, var(--blue-light) 100%);
  }
  .back__ring {
    position: absolute; left: 48px; top: 66px; width: 176px; height: 176px;
    border-radius: 50%; border: 2px solid rgba(255,255,255,0.6);
  }
  .back__dot {
    position: absolute; left: 62px; top: 80px; width: 148px; height: 148px;
    border-radius: 50%; background: var(--blue-deep);
    box-shadow: 0 4px 12px rgba(0,0,0,0.25);
  }
  .back__photo {
    position: absolute; left: 262px; top: 40px; width: 270px; height: 220px;
    background: radial-gradient(ellipse at 55% 50%, var(--photo-dark) 0%, var(--photo-grey) 55%, rgba(154,160,166,0) 100%);
  }
</style>
</head>
<body>
<main class="canvas">
  <section class="card card--front" aria-label="Business card front">
    <div class="front__top"></div>
    <div class="front__rule"></div>
    <div class="front__band"></div>
    <div class="brand">
      <span class="brand__dot"></span>
      <span class="brand__name">nimbora</span>
    </div>
    <div class="name-bar"><strong>Your Name,</strong><span>Title</span></div>
    <p class="address">Complex name, Street name<br>City, State, zip code</p>
    <div class="contact-divider"></div>
    <ul class="contacts">
      <li><svg viewBox="0 0 12 12"><path d="M2 1h3l1 3-2 1c1 2 2 3 3 3l1-2 3 1v3c-6 0-9-3-9-9z"/></svg>123-456-789</li>
      <li><svg viewBox="0 0 12 12"><rect x="3" y="0" width="6" height="12" rx="1"/></svg>123-456-789</li>
      <li><svg viewBox="0 0 12 12"><path d="M0 2h12v8H0z M0 2l6 5 6-5" /></svg>info@nimbora.com</li>
      <li><svg viewBox="0 0 12 12"><circle cx="6" cy="6" r="5.5"/></svg>www.nimbora.com</li>
    </ul>
  </section>

  <section class="card card--back" aria-label="Business card back">
    <div class="back__ring"></div>
    <div class="back__dot"></div>
    <div class="back__photo" role="img" aria-label="Photo of cars parked in street parking bays seen from above"></div>
  </section>
</main>
</body>
</html>
```